U.S. Popcorn company needs business cards

We are a popcorn company that manufactures popcorn and sells it to grocery stores worldwide. Our theme is "Americana" and our logo is U.S. route 66 which is the most famous highway in the U.S.

We would like the design to be simple and to use both sides. On the back side we would like to see just the logo and website. The front would be normal details

Target Market(s)

Wholesalers, grocers and distributors

Industry/Entity Type

Manufacture

Contact Information for Business Card

Business name: Prairie Lantern Popcorn
Phone: +1 555 308 4726
Email: Dale@prairielanternpopcorn.com
website: www.prairielanternpopcorn.com
Tag Line: "POPular for a reason"
Name: Dale Whitcombe
Title: Founder/President

Requirements
Must have
• Either this design should be fun or clean and simple. I will let you show me your thougths.
Nice to have
• Anything that ties in the real Hwy Route 66.
• Colors might need to be red, white and blue incorporated.
Should not have
• Not be too busy.

```html
<!DOCTYPE html>
<html lang="en">
<head>
<meta charset="utf-8">
<title>Prairie Lantern Popcorn – Business Cards</title>
<link rel="stylesheet" href="https://fonts.googleapis.com/css2?family=Lato:wght@400;700;900&display=swap">
<style>
  :root {
    --navy: #263a8c;
    --navy-deep: #1c2c73;
    --navy-light: #3447a3;
    --red: #e0303c;
    --white: #ffffff;
    --paper: #f4f4f4;
    --stage: #e6e4e0;
  }
  * { box-sizing: border-box; margin: 0; padding: 0; }
  html, body { width: 1200px; height: 780px; overflow: hidden; }
  body {
    background: var(--stage);
    font-family: "Lato", sans-serif;
    display: flex;
    align-items: center;
    justify-content: center;
    gap: 60px;
  }
  .card {
    width: 520px;
    height: 297px;
    position: relative;
    overflow: hidden;
    box-shadow: 0 6px 18px rgba(0,0,0,0.18);
  }

  /* Front */
  .card--front {
    background: linear-gradient(180deg, var(--white), var(--paper));
  }
  .front__brand {
    position: absolute;
    left: 34px; top: 50px;
    width: 190px;
    display: flex;
    align-items: center;
    gap: 12px;
  }
  .brand__dot {
    width: 18px; height: 18px;
    border-radius: 50%;
    background: var(--red);
    flex: none;
  }
  .brand__name {
    color: var(--navy);
    font-weight: 900;
    font-size: 24px;
    line-height: 1.1;
  }
  .front__divider {
    position: absolute;
    left: 238px; top: 36px;
    width: 1px; height: 160px;
    background: linear-gradient(180deg, rgba(224,48,60,0), var(--red) 50%, rgba(224,48,60,0));
  }
  .front__details {
    position: absolute;
    left: 262px; top: 30px;
    color: var(--navy);
  }
  .person__name { font-size: 22px; font-weight: 400; line-height: 1.1; }
  .person__title { font-size: 13px; color: var(--red); margin-bottom: 16px; }
  .address { font-size: 12px; line-height: 1.35; margin-bottom: 6px; }
  .contact { list-style: none; font-size: 11.5px; line-height: 1.55; }
  .contact li { display: flex; align-items: center; gap: 7px; }
  .contact svg { width: 12px; height: 12px; flex: none; }
  .front__rule {
    position: absolute;
    left: 0; right: 0; bottom: 60px;
    height: 2px;
    background: var(--red);
  }
  .front__band {
    position: absolute;
    left: 0; right: 0; bottom: 0;
    height: 56px;
    background: linear-gradient(180deg, var(--navy-light), var(--navy-deep));
    display: flex;
    align-items: center;
    justify-content: flex-end;
    padding-right: 28px;
  }
  .tagline { color: var(--white); font-size: 14px; letter-spacing: 0.3px; }

  /* Back */
  .card--back {
    background: radial-gradient(ellipse at 50% 40%, var(--navy-light), var(--navy-deep) 85%);
    display: flex;
    flex-direction: column;
    align-items: center;
    justify-content: center;
    gap: 22px;
  }
  .back__brand { display: flex; align-items: center; gap: 12px; }
  .back__brand .brand__name { color: var(--white); font-size: 28px; }
  .back__web { font-size: 13px; color: var(--white); letter-spacing: 0.3px; }
  .back__web .web__domain { color: var(--red); }
</style>
</head>
<body>
  <section class="card card--front" aria-label="Business card front">
    <div class="front__brand">
      <span class="brand__dot"></span>
      <span class="brand__name">Prairie Lantern Popcorn</span>
    </div>
    <div class="front__divider"></div>
    <div class="front__details">
      <p class="person__name">Dale Whitcombe</p>
      <p class="person__title">Founder/President</p>
      <p class="address">Maple Hollow, KS<br>United States</p>
      <ul class="contact">
        <li>
          <svg viewBox="0 0 12 12" aria-hidden="true"><rect width="12" height="12" fill="#e0303c"/><path d="M3.5 2.5h1.5l.7 2-1 .7a5 5 0 0 0 2.1 2.1l.7-1 2 .7v1.5c0 .5-.4.8-.9.8A6.5 6.5 0 0 1 2.7 3.4c0-.5.3-.9.8-.9z" fill="#fff"/></svg>
          +1 555 308 4726
        </li>
        <li>
          <svg viewBox="0 0 12 12" aria-hidden="true"><rect width="12" height="12" fill="#e0303c"/><rect x="2.5" y="3.5" width="7" height="5" fill="none" stroke="#fff" stroke-width="1"/><path d="M2.5 3.5 6 6.3l3.5-2.8" fill="none" stroke="#fff" stroke-width="1"/></svg>
          Dale@prairielanternpopcorn.com
        </li>
        <li>
          <svg viewBox="0 0 12 12" aria-hidden="true"><rect width="12" height="12" fill="#e0303c"/><circle cx="6" cy="6" r="3.5" fill="none" stroke="#fff" stroke-width="1"/><path d="M2.5 6h7M6 2.5c-1.6 2-1.6 5 0 7M6 2.5c1.6 2 1.6 5 0 7" fill="none" stroke="#fff" stroke-width=".8"/></svg>
          www.prairielanternpopcorn.com
        </li>
      </ul>
    </div>
    <div class="front__rule"></div>
    <div class="front__band"><span class="tagline">POPular for a reason</span></div>
  </section>

  <section class="card card--back" aria-label="Business card back">
    <div class="back__brand">
      <span class="brand__dot"></span>
      <span class="brand__name">Prairie Lantern Popcorn</span>
    </div>
    <p class="back__web">www.<span class="web__domain">prairielanternpopcorn</span>.com</p>
  </section>
</body>
</html>
```